Business Cards Design for the electrical wholesaler: clean bold dynamic :)

We need a business card design that would follow our latest brand guidelines. As an electrical wholesaler we want to bring a fresh look and feel into the industry. The design should be clean bold and dynamic. It should come alive with the renewed energy of our green colour. Our grey colour should keep things balanced and complement the notion of maturity and responsibility. We employ Lato as a corporate font however are not bound by this font and we’re open to interpretation here.

Target Market(s)

Electrical contractors

Industry/Entity Type

Business

Contact Information for Business Card

Logo
Name & Surname: Halyna Dorosh
Job Title: Director of Marketing
Email: halya.dorosh@quillmail.example
Cell phone: XXX.XXX.XXXX
Address: 20517 - 87 Ave. Edmonton, AB, Canada. T6K 4N8
Business Phone: 780.555.0184
Website: www.brovix.example

Font styles to use
Other font styles liked:
• Lato

Requirements
Must have
• Logo & website
Nice to have
• Brand elements - some of them you may find in the attached Brand Guidelines (e.g. three lines on the background signifying "W")

```html
<!DOCTYPE html>
<html lang="en">
<head>
<meta charset="utf-8">
<title>Brovix Business Card</title>
<link rel="stylesheet" href="https://fonts.googleapis.com/css2?family=Lato:wght@300;400;700;900&display=swap">
<style>
  :root {
    --bg: #3a3a3a;
    --bg-edge: #1c1c1c;
    --card: #2b2b2d;
    --card-edge: #232325;
    --brand-grey: #9a9a9c;
    --tag-grey: #6a6a6c;
    --green: #7cc520;
    --text: #f2f2f2;
  }
  * { box-sizing: border-box; margin: 0; padding: 0; }
  html, body { width: 799px; height: 1200px; overflow: hidden; }
  body {
    background: radial-gradient(ellipse at 60% 40%, var(--bg) 0%, var(--bg-edge) 100%);
    font-family: "Lato", sans-serif;
    position: relative;
  }
  .card {
    position: absolute;
    left: 120px;
    width: 560px;
    height: 320px;
    border-radius: 22px;
    background: linear-gradient(160deg, var(--card) 0%, var(--card-edge) 100%);
    box-shadow: 0 14px 30px rgba(0,0,0,0.55);
    overflow: hidden;
  }
  .card--front { top: 130px; }
  .card--back { top: 740px; }

  .brand {
    position: absolute;
    left: 150px;
    top: 100px;
  }
  .brand__row { display: flex; align-items: center; gap: 16px; }
  .brand__mark {
    width: 44px; height: 44px;
    background: var(--brand-grey);
  }
  .brand__name {
    font-weight: 400;
    font-size: 78px;
    line-height: 1;
    color: var(--brand-grey);
    letter-spacing: -1px;
  }
  .brand__tagline {
    margin-top: 8px;
    margin-left: 60px;
    font-size: 14px;
    letter-spacing: 3px;
    color: var(--tag-grey);
    text-transform: uppercase;
  }

  .contact {
    position: absolute;
    left: 0; right: 0; top: 44px;
    text-align: center;
    color: var(--text);
  }
  .contact__name {
    font-weight: 900;
    font-size: 28px;
    line-height: 1.15;
    color: var(--green);
  }
  .contact__title { font-size: 16px; margin-top: 2px; }
  .contact__icons {
    display: flex; justify-content: center; gap: 6px;
    margin-top: 18px;
  }
  .contact__icons svg { width: 16px; height: 16px; }
  .contact__line { font-size: 16px; line-height: 1.3; margin-top: 4px; }
  .contact__rule {
    position: absolute;
    left: 0; right: 0; top: 222px;
    height: 1px;
    background: var(--green);
  }
  .contact__address {
    position: absolute;
    left: 0; right: 0; top: 248px;
    text-align: center;
    font-size: 17px;
    color: var(--text);
  }
</style>
</head>
<body>
  <section class="card card--front">
    <div class="brand">
      <div class="brand__row">
        <span class="brand__mark"></span>
        <span class="brand__name">brovix</span>
      </div>
      <div class="brand__tagline">Electrical Wholesalers</div>
    </div>
  </section>

  <section class="card card--back">
    <div class="contact">
      <div class="contact__name">Halyna Dorosh</div>
      <div class="contact__title">Director of Marketing</div>
      <div class="contact__icons">
        <svg viewBox="0 0 16 16" aria-label="phone"><circle cx="8" cy="8" r="7.5" fill="var(--green)"/><path d="M5 4.5l1.6-.5 1 2-1 .8a5 5 0 0 0 2.6 2.6l.8-1 2 1-.5 1.6c-3.6.2-6.7-2.9-6.5-6.5z" fill="#2b2b2d"/></svg>
        <svg viewBox="0 0 16 16" aria-label="email"><circle cx="8" cy="8" r="7.5" fill="var(--green)"/><rect x="4" y="5" width="8" height="6" fill="#2b2b2d"/><path d="M4 5l4 3.2L12 5" stroke="var(--green)" stroke-width="0.9" fill="none"/></svg>
        <svg viewBox="0 0 16 16" aria-label="website"><circle cx="8" cy="8" r="7.5" fill="var(--green)"/><circle cx="8" cy="8" r="4" fill="none" stroke="#2b2b2d" stroke-width="1.1"/><path d="M4 8h8M8 4c-2 2.4-2 5.6 0 8M8 4c2 2.4 2 5.6 0 8" stroke="#2b2b2d" stroke-width="0.9" fill="none"/></svg>
      </div>
      <div class="contact__line">+1 780-555-0184</div>
      <div class="contact__line">halya.dorosh@quillmail.example | www.brovix.example</div>
    </div>
    <div class="contact__rule"></div>
    <div class="contact__address">20517 - 87 Ave. Edmonton, AB, Canada T6K 4N8</div>
  </section>
</body>
</html>
```